professional business card design

Business card design. Photos have been uploaded and i am open to the designer choosing which photos to use. Would like the card to be mostyly in a grey scale design with black, whites, silver & grey colours. I have added copy of our flyer as would like on the back side of card our services to be listed. Do not use any bright colurs such as blue red green or yellow. i need to be able to edit the phone number and naem in the final card design submitted.

Target Market(s)

Clients

Industry/Entity Type

earhmovibng and transport

Contact Information for Business Card

Director Name, address, email, phone number and services

Colors

Designer to choose only greyscale colors for use in the design.

Requirements
Should not have
• no yellow, red, blue or green

```html
<!DOCTYPE html>
<html lang="en">
<head>
<meta charset="utf-8">
<title>Carrow Haul Business Card</title>
<link href="https://fonts.googleapis.com/css2?family=Archivo+Black&family=Roboto:ital,wght@0,400;0,700;1,400;1,700&display=swap" rel="stylesheet">
<style>
  :root {
    --page: #cfcfcf;
    --black: #0b0b0b;
    --charcoal: #1d1d1d;
    --white: #ffffff;
    --silver-light: #e4e4e4;
    --silver: #b9b9b9;
    --silver-dark: #8e8e8e;
    --text-soft: #d6d6d6;
    --earth-dark: #3a2a1c;
    --earth: #a5764a;
    --sky-pale: #d7dde2;
    --sky-grey: #9aa3aa;
  }
  * { box-sizing: border-box; margin: 0; padding: 0; }
  html, body { width: 1200px; height: 800px; overflow: hidden; }
  body {
    background: var(--page);
    display: flex;
    align-items: center;
    justify-content: center;
    gap: 24px;
    font-family: "Roboto", Arial, sans-serif;
  }
  .card {
    position: relative;
    width: 566px;
    height: 324px;
    overflow: hidden;
    background: radial-gradient(ellipse at 45% 35%, var(--charcoal), var(--black) 75%);
    box-shadow: 0 8px 22px rgba(0,0,0,.35);
  }

  /* Front */
  .front-photo {
    position: absolute;
    left: 0; top: 70px;
    width: 566px; height: 168px;
    background: linear-gradient(180deg, var(--black) 0%, var(--earth-dark) 40%, var(--earth) 70%, var(--earth-dark) 100%);
    opacity: .9;
  }
  .brand {
    position: absolute;
    left: 28px; top: 24px;
    display: flex; align-items: center; gap: 10px;
    font-family: "Archivo Black", Arial, sans-serif;
    font-size: 30px;
    color: var(--silver-light);
    letter-spacing: .5px;
  }
  .brand-dot {
    width: 16px; height: 16px; border-radius: 50%;
    background: var(--silver);
  }
  .phone {
    position: absolute;
    left: 22px; top: 196px;
    display: flex; align-items: center; gap: 10px;
    font-family: "Archivo Black", Arial, sans-serif;
    font-size: 30px;
    color: var(--white);
    letter-spacing: 1px;
  }
  .phone svg { width: 26px; height: 26px; }
  .silver-line {
    position: absolute; left: 0; top: 238px;
    width: 566px; height: 6px;
    background: linear-gradient(90deg, var(--silver-dark), var(--silver-light), var(--silver));
  }
  .contact-band {
    position: absolute; left: 0; top: 244px;
    width: 566px; height: 48px;
    background: var(--black);
    display: flex; align-items: center;
    padding: 0 22px;
  }
  .person { color: var(--white); }
  .person-name {
    font-family: "Archivo Black", Arial, sans-serif;
    font-size: 20px; line-height: 1;
  }
  .person-title { font-size: 14px; margin-top: 3px; }
  .band-divider {
    width: 1px; height: 34px; background: var(--silver-dark);
    margin: 0 16px;
  }
  .web-contacts { color: var(--white); font-size: 14px; line-height: 1.4; }
  .web-contacts div { display: flex; align-items: center; gap: 7px; }
  .web-contacts svg { width: 14px; height: 14px; }
  .address-band {
    position: absolute; left: 0; top: 292px;
    width: 566px; height: 32px;
    background: linear-gradient(90deg, var(--silver), var(--silver-light) 50%, var(--silver));
    color: var(--black);
    font-size: 16px;
    display: flex; align-items: center;
    padding-left: 90px;
  }

  /* Back */
  .back-photo {
    position: absolute;
    left: 312px; top: 48px;
    width: 420px; height: 420px;
    border-radius: 50%;
    background: linear-gradient(180deg, var(--sky-pale) 0%, var(--sky-grey) 45%, #6f6f6f 70%, #4a4a4a 100%);
  }
  .services {
    position: absolute; left: 22px; top: 18px;
    list-style: none;
    color: var(--white);
    font-size: 14.5px;
    line-height: 17.5px;
  }
  .services li { display: flex; align-items: center; gap: 8px; }
  .services li::before {
    content: ""; width: 7px; height: 7px; border-radius: 50%;
    background: var(--white); flex: none;
  }
  .services li.faded { color: var(--text-soft); opacity: .55; }
  .services li.faded::before { background: var(--silver-dark); }
  .call-to-action {
    position: absolute; left: 22px; top: 238px;
    width: 276px;
    color: var(--white);
    font-size: 15px;
    line-height: 19px;
  }
  .call-to-action em { font-style: italic; font-weight: 400; }
  .call-to-action strong { font-weight: 700; }
</style>
</head>
<body>

<section class="card card-front">
  <div class="front-photo" role="img" aria-label="Photo of a road train with trailers on red earth at dusk"></div>
  <div class="brand"><span class="brand-dot"></span>Carrow Haul</div>
  <div class="phone">
    <svg viewBox="0 0 24 24" fill="none" stroke="currentColor" stroke-width="2.4" stroke-linecap="round"><path d="M6 3l3 4-2 2c1 3 4 6 7 7l2-2 4 3-2 3C10 20 4 14 3 6z"/></svg>
    055.274 618 930
  </div>
  <div class="silver-line"></div>
  <div class="contact-band">
    <div class="person">
      <div class="person-name">DANIEL HARPER</div>
      <div class="person-title">Managing Director</div>
    </div>
    <div class="band-divider"></div>
    <div class="web-contacts">
      <div><svg viewBox="0 0 16 16" fill="none" stroke="currentColor" stroke-width="1.6"><rect x="1" y="3" width="14" height="10"/><path d="M1 3l7 6 7-6"/></svg>hello@carrowhaul.com</div>
      <div><svg viewBox="0 0 16 16" fill="none" stroke="currentColor" stroke-width="1.4"><circle cx="8" cy="8" r="6.5"/><path d="M1.5 8h13M8 1.5c-3 3.5-3 9.5 0 13M8 1.5c3 3.5 3 9.5 0 13"/></svg>www.carrowhaul.com</div>
    </div>
  </div>
  <div class="address-band">87 Quarry Road, Brookvale, 60318</div>
</section>

<section class="card card-back">
  <div class="back-photo" role="img" aria-label="Photo of a white prime mover carrying a grader on a low loader"></div>
  <ul class="services">
    <li class="faded">Hot shot loads</li>
    <li class="faded">Vehicle recovery services</li>
    <li class="faded">Potable water deliveries</li>
    <li class="faded">Road building/mainttenance</li>
    <li class="faded">Earthworks</li>
    <li>Sand &amp; metal supply &amp; cartage</li>
    <li>Road train tippers</li>
    <li>Road train tankers</li>
    <li>Road train flat tops</li>
    <li>Drop deck trailers</li>
    <li>Mine site accredited</li>
    <li>Equipment &amp; operators</li>
  </ul>
  <p class="call-to-action"><em>we offer a large range of services not listed</em> <strong>so call us today for a personalised quote to suit your needs.</strong></p>
</section>

</body>
</html>
```